Business cards and stationary design

We just completed the design of our new logo and we need to print new business cards and letterhead for our nonprofit. We are looking for a fresh new design that shows off our new logo. On letterhead, we must have a column on the right or left to include our Board of Directors (up to 45 names) (see attachment)

Industry/Entity Type

Non-Profit

Contact Information for Business Card

Standard business card with name, title, Company name, mailing address phone numbers, email address and website. Tagline on back "Bringing the homeless home"

Font styles to use
Sans Serif

Requirements
Must have
• include pertinent information above
• new logo
• fonts compatible with logo
• should use logo colors only
Nice to have
• tag lines

```html
<!DOCTYPE html>
<html lang="en">
<head>
<meta charset="utf-8">
<title>Shelter Path Center – Business Card</title>
<link href="https://fonts.googleapis.com/css2?family=Exo+2:wght@400;500;600&display=swap" rel="stylesheet">
<style>
  :root {
    --page-bg: #d8d3ce;
    --panel-deep: #0f4660;
    --panel-mid: #1d6b88;
    --panel-light: #2b7f98;
    --frost: #eef2f3;
    --frost-shade: #d9e1e4;
    --accent: #e6960f;
    --text-light: #e7f0f4;
    --brand-teal: #1b4f6a;
  }
  * { margin: 0; padding: 0; box-sizing: border-box; }
  html, body {
    width: 1200px; height: 969px; overflow: hidden;
    background: var(--page-bg);
    font-family: "Exo 2", Arial, sans-serif;
  }
  .business-card {
    position: absolute; left: 100px; top: 200px;
    width: 1000px; height: 568px;
    background: linear-gradient(160deg, var(--frost) 0%, var(--frost-shade) 100%);
    box-shadow: 0 12px 30px rgba(0,0,0,0.18);
    overflow: hidden;
  }
  .card-shapes { position: absolute; inset: 0; }
  .contact-block {
    position: absolute; left: 65px; top: 128px;
    color: var(--text-light);
  }
  .person-name {
    font-size: 34px; font-weight: 500; letter-spacing: 3px;
    color: var(--accent); line-height: 1;
  }
  .person-title {
    margin-top: 8px; font-size: 21px; letter-spacing: 2px; line-height: 1;
  }
  .mailing-address {
    margin-top: 30px; font-size: 22px; line-height: 29px; font-style: normal;
  }
  .contact-list { margin-top: 30px; list-style: none; }
  .contact-list li {
    display: flex; align-items: center; gap: 14px;
    font-size: 21px; line-height: 32px;
  }
  .contact-list svg { width: 20px; height: 20px; flex: none; }
  .brand-name {
    position: absolute; left: 540px; top: 240px; width: 420px;
    text-align: center; color: var(--brand-teal);
    font-size: 36px; font-weight: 600; letter-spacing: 3px; line-height: 1.2;
  }
  .brand-name .brand-sub { display: block; font-size: 22px; letter-spacing: 6px; }
</style>
</head>
<body>
  <div class="business-card">
    <svg class="card-shapes" viewBox="0 0 1000 568" width="1000" height="568">
      <defs>
        <linearGradient id="panelGradient" x1="0" y1="0" x2="1" y2="1">
          <stop offset="0" stop-color="var(--panel-mid)"/>
          <stop offset="0.45" stop-color="var(--panel-deep)"/>
          <stop offset="1" stop-color="var(--panel-light)"/>
        </linearGradient>
      </defs>
      <polygon class="info-panel" points="0,0 688,0 407,284 688,568 0,568" fill="url(#panelGradient)"/>
      <polyline class="chevron-stripe" points="712,-4 428,284 712,572" fill="none" stroke="var(--accent)" stroke-width="7"/>
    </svg>

    <div class="contact-block">
      <p class="person-name">DANIEL REYES</p>
      <p class="person-title">CEO/FOUNDER</p>
      <address class="mailing-address">
        Shelter path center<br>
        2140 Birchwood Avenue<br>
        Fairbanks, Alaska 99701
      </address>
      <ul class="contact-list">
        <li>
          <svg viewBox="0 0 20 20" aria-hidden="true"><path d="M4 2 l3 0 l2 4 l-2 2 q2 4 5 5 l2 -2 l4 2 l0 3 q-1 2 -3 2 q-8 -1 -13 -9 q-1 -4 2 -7z" fill="var(--accent)"/></svg>
          555 204 7186
        </li>
        <li>
          <svg viewBox="0 0 20 20" aria-hidden="true"><rect x="1" y="4" width="18" height="12" fill="var(--accent)"/><polyline points="1,4 10,11 19,4" fill="none" stroke="var(--panel-deep)" stroke-width="1.5"/></svg>
          daniel@shelterpathcenter.org
        </li>
        <li>
          <svg viewBox="0 0 20 20" aria-hidden="true"><circle cx="10" cy="10" r="8.5" fill="var(--accent)"/><path d="M6 6 q3 1 2 4 q-2 1 -1 4 M12 4 q-1 3 2 4 q2 0 2 3" fill="none" stroke="var(--panel-deep)" stroke-width="1.4"/></svg>
          www.shelterpathcenter.org
        </li>
      </ul>
    </div>

    <p class="brand-name">SHELTER PATH<span class="brand-sub">CENTER</span></p>
  </div>
</body>
</html>
```